Redesign company trifold brochure

We are rebranding our company in September and looking for a more professional design for our brochure.

What we do - providing interdisciplinary care for those supporting ill, elderly and special needs pets at home following the human hospice model of care - is very novel and our brochure is key in explaining it and our offerings.

We serve dogs and cats. Most of the animals are quite sick, elderly. I have many personal and stock photos we can use in the brochure. Please - no pictures of puppies and/or kittens.

The hard part is fitting the info and message into a clear and concise format.

It must be appealing both to pet owners and vets (who are our primary source of patients through referrals).

It should covey WARMTH, COMPASSION, PROFESSIONALISM, and EXPERTISE.

Please look at our website www.TrellisAnimalRespite.com for more info

We have until now used maroon and copper for colors - to reflect the "sunset" of the pets life. BUT are now changing to Navy, Teal and White to reflect calm, trust and competence.

We will use the same logo recolored.

Existing brochure and new logo are attached.

PLEASE ask questions!!
Updates

We have a library of stock images you are welcome to use. All have been legally acquired and we have the right to use them. You DO NOT have to use them, just sending along in case you wish to. https://www.filecrate.example/sh/qk4vrm82zd1pyno/KLQ7Ztbn-Rrfx2mh9sWpYJ4Dc?dl=0

Our colors are NAVY, TEAL and WHITE. For your reference, the navy we use is 99/87/44/55 (CMYK) The Teal we use is 76/11/44/0 (CMYK) Thank you!

Designers -- pleaseuse pictures of older pets (no puppies or kittens). Below is a link to stock photos we own that would be appropriate for use in the brochure. https://www.filecrate.example/sh/w274m6t9pxkr5da/KLRn3GsfwlTVBXEPcq_8ZNj5u?dl=0 THANK YOU!

Designers -- I would VERY much like to include a photo of a pet in a wheel chair. I have personal photos as well as (purchased) stock photos for this purpose which can be found at http://lnk.example/TARHC-Pets-in-Wheelchairs Thank you!!

Today is the last day! Many of you have submitted beautiful designs and others are rolling in. I am so appreciative of your time and energy!! Please do not let the deadline pass without YOUR very BEST entry being submitted!! Thank you! - Miriam & All of us at Trellis Animal Respite & Home Care

Target Market(s)

Pet Owners and Veterinarians

Industry/Entity Type

Pet Care

Font styles to use
Serif

Colors
0455a3
33b8a4
ffffff

Requirements
Must have
• Our logo and information about our services. Pictures of pets. Our contact info. PLEASE NOTE: this is a 2 sided brochure. Please submit both inside and outside.
Should not have
• puppies, kittens - anything off message

```html
<!DOCTYPE html>
<html lang="en">
<head>
<meta charset="utf-8">
<title>Trellis Animal Respite &amp; Home Care — Inside Spread</title>
<link href="https://fonts.googleapis.com/css2?family=Marcellus&family=Crimson+Pro:ital,wght@0,400;0,600;1,600;1,700&display=swap" rel="stylesheet">
<style>
  :root{
    --navy:#0f1c4d;
    --teal:#2aa39a;
    --teal-light:#45bcb0;
    --teal-text:#1f9a8c;
    --white:#ffffff;
    --paper:#f4f7fa;
    --ink:#1c2340;
    --lavender:#e9e4f4;
    --heading-font:"Marcellus", "Times New Roman", serif;
    --body-font:"Crimson Pro", Georgia, serif;
  }
  *{margin:0;padding:0;box-sizing:border-box}
  html,body{width:1200px;height:895px;overflow:hidden;background:var(--white)}
  body{font-family:var(--body-font);color:var(--ink)}
  .spread{position:relative;width:1200px;height:895px;overflow:hidden}
  .panel{position:absolute;top:0;height:895px;width:400px;overflow:hidden}
  .panel--care{left:0}
  .panel--team{left:400px}
  .panel--services{left:800px;background:linear-gradient(90deg,#eef1f5,var(--white) 30%)}
  .layer{position:absolute;left:0;top:0}
  .abs{position:absolute}

  .panel-title{font-family:var(--heading-font);font-weight:400;color:var(--navy);text-align:center;line-height:1.08}
  .care-title{left:35px;top:30px;width:330px;font-size:34px}
  .care-copy{left:40px;width:330px;font-size:16px;line-height:1.28}
  .care-copy b{font-style:italic;font-weight:700;color:var(--navy)}
  .care-copy--palliative{top:120px}
  .care-copy--hospice{top:196px}

  .photo-circle{border-radius:50%;border:6px solid var(--navy);overflow:hidden}
  .photo-circle--vets{left:36px;top:356px;width:172px;height:172px;background:radial-gradient(circle at 50% 45%,#f3f1ec,#a9c9dc 60%,#6e8fa6)}
  .photo-circle--dalmatian{left:232px;top:748px;width:112px;height:112px;border:5px solid var(--white);background:radial-gradient(circle at 50% 40%,#f6f6f6,#c8c8c8 70%,#8a8a8a)}

  .teal-heading{font-style:italic;font-weight:700;font-size:19px;line-height:1.2}
  .bullets{list-style:none}
  .bullets li{position:relative;padding-left:18px}
  .bullets li::before{content:"";position:absolute;left:2px;top:.5em;width:8px;height:8px;border-radius:50%;background:currentColor;opacity:.85}

  .care-heading{left:40px;top:546px;color:var(--lavender)}
  .care-list{left:40px;top:580px;width:330px;color:var(--white);font-size:15px;line-height:19px}
  .care-list li{margin-bottom:11px}

  .brand{left:60px;top:806px;display:flex;align-items:center;gap:12px;color:var(--white);font-weight:600;font-size:19px;line-height:1.1}
  .brand-mark{width:34px;height:34px;border-radius:50%;background:var(--teal);flex:none}

  .team-title{left:0;top:488px;width:400px;font-size:30px}
  .team-intro{left:40px;top:530px;width:330px;color:var(--navy);font-size:18px}
  .team-list{left:40px;top:584px;width:330px;color:var(--white);font-size:15px;line-height:21.5px}

  .services-title{left:40px;top:28px;width:340px;font-size:32px}
  .services-copy{left:42px;width:338px;font-size:15px;line-height:19px}
  .services-copy--intro{top:86px}
  .services-copy--team{top:218px}
  .services-callout{left:42px;top:160px;width:338px;color:var(--teal-text)}
  .services-list{left:42px;top:320px;width:330px;font-size:15px;line-height:18px}
  .services-list li::before,.extras-list li::before{background:var(--teal)}
  .extras-heading{left:42px;top:602px;color:var(--teal-text);font-size:16px}
  .extras-list{left:126px;top:630px;width:260px;font-size:15px;line-height:19px}
  .photo-block{border-radius:4px}
  .photo-block--wheelchair{left:250px;top:508px;width:135px;height:80px;background:linear-gradient(135deg,#f2f2f2,#c9a88a 45%,#6b4aa0 70%,#e8e8e8)}
  .photo-block--cat{left:22px;top:672px;width:94px;height:160px;background:linear-gradient(180deg,#8d8178,#5d5650 55%,#b06a35 80%,#8a4f24)}
</style>
</head>
<body>
<main class="spread">

  <svg class="layer" width="800" height="895" viewBox="0 0 800 895" role="img" aria-label="Photograph of a dog and a cat resting together on a bed">
    <defs>
      <linearGradient id="hero-tone" x1="0" y1="0" x2="1" y2="1">
        <stop offset="0" stop-color="#c9d6e2"/>
        <stop offset=".45" stop-color="#8a6a4e"/>
        <stop offset=".75" stop-color="#3b2c22"/>
        <stop offset="1" stop-color="#a37b56"/>
      </linearGradient>
      <linearGradient id="hero-fade" x1="0" y1="0" x2="0" y2="1">
        <stop offset="0" stop-color="#f4f7fa" stop-opacity="1"/>
        <stop offset="1" stop-color="#f4f7fa" stop-opacity="0"/>
      </linearGradient>
    </defs>
    <rect x="0" y="0" width="400" height="270" fill="#f4f7fa"/>
    <path d="M0,270 L400,270 L400,0 L800,0 L800,520 L0,520 Z" fill="url(#hero-tone)"/>
    <rect x="0" y="268" width="400" height="50" fill="url(#hero-fade)"/>
  </svg>

  <section class="panel panel--care">
    <svg class="layer" width="400" height="895" viewBox="0 0 400 895" aria-hidden="true">
      <path d="M0,468 C120,486 260,486 400,472 V895 H0 Z" fill="var(--teal)"/>
      <path d="M0,474 C120,492 260,492 400,478" fill="none" stroke="#ffffff" stroke-width="3"/>
      <path d="M0,778 C140,764 280,766 400,776 V895 H0 Z" fill="var(--navy)"/>
      <path d="M0,772 C140,758 280,760 400,770" fill="none" stroke="#ffffff" stroke-width="4"/>
    </svg>
    <h1 class="abs panel-title care-title">Palliative Care<br>&amp; Hospice</h1>
    <p class="abs care-copy care-copy--palliative"><b>Palliative Care</b> seeks to relieve suffering and improve quality of life at all stages of illness, injury and disease, whether curable or not.</p>
    <p class="abs care-copy care-copy--hospice"><b>Hospice</b> is a special kind of Palliative Care focused on those with a life expectancy of less than one year.</p>
    <div class="abs photo-circle photo-circle--vets" role="img" aria-label="Photograph of two veterinarians with a dog"></div>
    <h2 class="abs teal-heading care-heading">Both Palliative Care and Hospice:</h2>
    <ul class="abs bullets care-list">
      <li>Focus on living fully</li>
      <li>Recognize and address all suffering - physical, emotional, social and spiritual</li>
      <li>Use a team approach to meet the needs of the animal and his or her family</li>
      <li>Affirm life while viewing death as a natural, normal process</li>
    </ul>
    <div class="abs brand"><span class="brand-mark"></span><span>Trellis Animal Respite<br>&amp; Home Care</span></div>
  </section>

  <section class="panel panel--team">
    <svg class="layer" width="400" height="895" viewBox="0 0 400 895" aria-hidden="true">
      <path d="M0,472 C140,466 280,460 400,452 V895 H0 Z" fill="var(--teal)"/>
      <path d="M0,472 C140,466 280,460 400,452 V520 C280,528 140,526 0,522 Z" fill="var(--teal-light)" opacity=".5"/>
      <path d="M0,478 C140,472 280,466 400,458" fill="none" stroke="#ffffff" stroke-width="3"/>
      <path d="M0,790 C130,798 260,800 400,780 V895 H0 Z" fill="var(--navy)"/>
      <path d="M0,784 C130,792 260,794 400,774" fill="none" stroke="#ffffff" stroke-width="4"/>
    </svg>
    <h2 class="abs panel-title team-title">Our Team</h2>
    <p class="abs teal-heading team-intro">Lead by Miriam Okafor, C.T. our interdisciplinary team includes:</p>
    <ul class="abs bullets team-list">
      <li>Certified Thanatologist</li>
      <li>Certified Veterinary Technicians</li>
      <li>Interfaith Spiritual Advisor</li>
      <li>Certified Small Animal Massage Therapist</li>
      <li>Animal Care Specialists</li>
      <li>Hospice Assistants</li>
      <li>Client Care Coordinator</li>
    </ul>
    <div class="abs photo-circle photo-circle--dalmatian" role="img" aria-label="Photograph of a dalmatian"></div>
  </section>

  <section class="panel panel--services">
    <svg class="layer" width="400" height="895" viewBox="0 0 400 895" aria-hidden="true">
      <path d="M0,0 H14 C34,300 34,600 14,895 H0 Z" fill="var(--navy)"/>
      <path d="M14,0 C34,300 34,600 14,895" fill="none" stroke="#c7cfe0" stroke-width="2"/>
    </svg>
    <h2 class="abs panel-title services-title">Our Services</h2>
    <p class="abs services-copy services-copy--intro">At Trellis Animal Respite &amp; Home Care, our only goal is to support you in providing the very best care for your beloved companion in your own home.</p>
    <p class="abs teal-heading services-callout">We are here for you 24 hours a day, every day of the year.</p>
    <p class="abs services-copy services-copy--team">We work as a team to address the needs of your entire family. We come with no agenda and no prescribed plan, but rather follow your needs and wishes as they evolve and change over time. Some of the services we offer are:</p>
    <ul class="abs bullets services-list">
      <li>Visiting and support</li>
      <li>Administration of medication &amp; fluids</li>
      <li>Overnight and respite care</li>
      <li>Check-ins, exercise and play</li>
      <li>Assistance evaluating pain, quality of life, and end of life choices</li>
      <li>Coordination of care with your vet and other care professionals</li>
      <li>Home cooked meals and treats</li>
      <li>Transportation and errand running</li>
      <li>Equipment and supplies</li>
      <li>Funerals and memorials</li>
      <li>Bereavement support</li>
    </ul>
    <div class="abs photo-block photo-block--wheelchair" role="img" aria-label="Photograph of a beagle using a pet wheelchair"></div>
    <p class="abs teal-heading extras-heading">Our skilled team members can also provide:</p>
    <div class="abs photo-block photo-block--cat" role="img" aria-label="Photograph of a grey cat sitting on a wooden floor"></div>
    <ul class="abs bullets extras-list">
      <li>Massage and CalmTouch</li>
      <li>Cold LASER Treatments</li>
      <li>Reiki</li>
      <li>Passive Range of Motion (PROM)</li>
      <li>Rehabilitation Support</li>
      <li>Grooming</li>
      <li>Essential Oils</li>
      <li>Meadow Flower Essences</li>
      <li>Aroma Therapy</li>
      <li>Music Therapy</li>
      <li>Pet Therapy</li>
    </ul>
  </section>

</main>
</body>
</html>
```